Wed site for biomedical device startup

We need a generic website for a medical device startup. I will provide examples below of websites from other companies that can serve as models for what we are looking for. The startup is for a device that can non invasively measure blood flow in the brain using light. The application is to detect the type of stroke someone is having before they get to the hospital so treatment can be started right away. This saves patients upto hours of delayed treatment. Patients will be able to recover from stroke much better and faster as a result. I have attached an AI generated illustration of what the device will ultimately look like for reference.

https://www.372clinicaltech.com
https://vextalune.com

Target Market(s)

Biomedical, medical device, investors of biomedical device startups

Industry/Entity Type

Biomedical

Coding

Coded - Design and coding required

Number of Pages Required

4 page

Requirements
Must have
• same section and section headings as example websites listed above
Nice to have
• similar to example websites listed above. Prefer a darker website over a lighter one. Perhaps dark blues to go with logo colors. A moving background image element at top of landing page could be cool. Something indicative of heartbeat, or neurons, or blood flow.

```html
<!DOCTYPE html>
<html lang="en">
<head>
<meta charset="utf-8">
<title>LUMEVA — Smart Blood Loss Monitoring</title>
<link href="https://fonts.googleapis.com/css2?family=Michroma&family=Roboto:wght@400;500;700&display=swap" rel="stylesheet">
<style>
:root{
  --navy:#05053a;
  --navy-soft:#0c0b4c;
  --cyan:#22c3e6;
  --blue:#4a7fe0;
  --violet:#8b35d0;
  --white:#ffffff;
  --muted:#b9bce0;
  --line:#2a3a8a;
  --grad:linear-gradient(90deg,var(--cyan),var(--violet));
}
*{box-sizing:border-box;margin:0;padding:0}
html,body{width:1200px;height:4515px;overflow:hidden;background:var(--navy);color:var(--white);font-family:'Roboto',Arial,sans-serif}
.page{position:relative;width:1200px;height:4515px;overflow:hidden}
.abs{position:absolute}
.display{font-family:'Michroma',Arial,sans-serif;font-weight:400;letter-spacing:1.5px}
.grad-text{background:var(--grad);-webkit-background-clip:text;background-clip:text;color:transparent}
.btn{position:absolute;display:flex;align-items:center;justify-content:center;border-radius:30px;background:var(--grad);font-family:'Michroma',Arial,sans-serif;font-size:15px;letter-spacing:1.5px;color:var(--white)}
.brand{position:absolute;display:flex;align-items:center;gap:12px;font-family:'Michroma',Arial,sans-serif;color:var(--white)}
.brand-dot{border-radius:50%;background:var(--grad)}
.body-copy{font-size:14px;line-height:23px;color:var(--white)}
.photo{position:absolute}
.ring{position:absolute;border-radius:50%;border:3px solid rgba(160,180,255,.75)}

.nav a{position:absolute;top:44px;font-family:'Michroma',Arial,sans-serif;font-size:12.5px;letter-spacing:.5px;color:var(--white);text-decoration:none}
.nav .active:after{content:"";position:absolute;left:0;right:0;top:24px;height:3px;background:var(--cyan);border-radius:2px}

.hero-title{left:122px;top:284px;font-size:31px;line-height:43px}

.feature{position:absolute;width:290px;text-align:center}
.feature-icon{margin:0 auto;width:136px;height:136px;border-radius:50%;border:4px solid;border-color:var(--cyan) var(--violet) var(--violet) var(--cyan);display:flex;align-items:center;justify-content:center;background:var(--navy-soft)}
.feature h3{margin-top:28px;font-size:19px;font-weight:700}
.feature p{margin-top:14px;font-size:14px;line-height:21px;color:var(--muted)}

.checks{list-style:none}
.checks li{display:flex;align-items:center;gap:6px;font-size:14px;line-height:28px}
.checks li:before{content:"";width:9px;height:9px;border-radius:50%;background:var(--white);outline:2px solid var(--white);outline-offset:1px;transform:scale(.8)}

.member{position:absolute;width:240px;text-align:center}
.avatar{margin:0 auto;width:212px;height:212px;border-radius:50%;background:var(--grad);padding:8px}
.avatar div{width:100%;height:100%;border-radius:50%;background:linear-gradient(160deg,#cfd6de,#6b7786)}
.member h4{margin-top:30px;font-size:19px;font-weight:500;line-height:25px}

.field{position:absolute;border:1.5px solid var(--white);border-radius:20px;font-size:14px;padding:12px 14px;color:var(--white)}

.foot-col h5{font-family:'Michroma',Arial,sans-serif;font-weight:400;font-size:15px;letter-spacing:1px;margin-bottom:22px}
.foot-col p{font-size:15px;margin-bottom:18px;display:flex;align-items:center;gap:12px}
.social{position:absolute;top:4418px;width:48px;height:48px;border-radius:50%;background:var(--grad)}
</style>
</head>
<body>
<div class="page">

  <section class="hero">
    <div class="abs" style="left:0;top:0;width:1200px;height:96px;background:var(--navy)"></div>
    <svg class="abs" style="left:0;top:96px" width="1200" height="620" viewBox="0 0 1200 620">
      <defs>
        <linearGradient id="heroBg" x1="0" y1="0" x2="0" y2="1">
          <stop offset="0" stop-color="#0b0b42"/><stop offset="1" stop-color="#1a1560"/>
        </linearGradient>
        <linearGradient id="heroLine" x1="0" y1="0" x2="1" y2="0">
          <stop offset="0" stop-color="#22c3e6"/><stop offset="1" stop-color="#8b35d0"/>
        </linearGradient>
      </defs>
      <path d="M0 0H1200V500Q600 660 0 500Z" fill="url(#heroBg)"/>
      <path d="M95 538Q600 680 1075 545Q600 640 95 538Z" fill="url(#heroLine)"/>
    </svg>
    <div class="photo" role="img" aria-label="Hero illustration of a glowing anatomical heart with a heartbeat trace"
      style="left:600px;top:96px;width:600px;height:540px;background:linear-gradient(90deg,rgba(26,22,100,0) 0%,rgba(60,70,190,.55) 35%,rgba(90,80,210,.55) 70%,rgba(30,40,130,.4) 100%)"></div>

    <div class="brand" style="left:128px;top:22px;font-size:32px">
      <span class="brand-dot" style="width:56px;height:56px"></span>LUMEVA
    </div>
    <nav class="nav">
      <a class="active" style="left:482px">HOME</a>
      <a style="left:582px">ABOUT</a>
      <a style="left:690px">TECHNOLOGY</a>
      <a style="left:868px">PRESS</a>
      <a style="left:975px">CONTACT</a>
    </nav>
    <h1 class="display abs hero-title">SMART BLOOD<br>LOSS MONITORING</h1>
    <a class="btn" style="left:126px;top:408px;width:176px;height:57px">CONTACT</a>
  </section>

  <section class="help">
    <div class="abs" style="left:95px;top:910px;width:325px;height:298px;border:4px solid var(--cyan)"></div>
    <div class="abs" style="left:108px;top:924px;width:300px;height:268px;border:4px solid var(--violet)"></div>
    <div class="photo" role="img" aria-label="Clinician attaching a forehead sensor to a patient"
      style="left:126px;top:822px;width:462px;height:352px;background:linear-gradient(120deg,#e6e8ec,#b9c0c9 55%,#8e98a6)"></div>
    <h2 class="display grad-text abs" style="left:645px;top:855px;font-size:29px">HOW WE HELP</h2>
    <p class="body-copy abs" style="left:646px;top:912px;width:430px">During the first days of life, a significant risk of permanent injury exists from ventricular hemorrhage (IVH), caused by rupture of immature blood vessels in the brain due to excessive flow. There is a clear link between excessive fluctuations in blood flow and subsequent development of IVH.</p>
    <p class="body-copy abs" style="left:646px;top:1052px;width:410px">CEREFLO¹ is a continuous intracranial blood flow sensor designed to provide real-time monitoring of blood flow, providing clinicians with an early warning signal to potentially mitigate permanent</p>
  </section>

  <section class="tech">
    <div class="abs" style="left:0;top:1305px;width:1200px;height:1px;background:var(--line)"></div>
    <div class="abs" style="left:770px;top:1306px;width:430px;height:538px;background:linear-gradient(120deg,var(--cyan),var(--blue) 50%,var(--violet))"></div>
    <svg class="abs" style="left:580px;top:1306px" width="320" height="538" viewBox="0 0 320 538" aria-hidden="true">
      <path d="M190 0Q260 60 260 270Q260 470 190 538H0V0Z" fill="var(--navy)"/>
    </svg>
    <div class="ring" style="left:627px;top:1394px;width:400px;height:400px"></div>
    <div class="ring" style="left:645px;top:1412px;width:364px;height:364px;border-width:2px"></div>
    <div class="photo" role="img" aria-label="Woman wearing a forehead blood flow sensor with a handheld monitor"
      style="left:678px;top:1445px;width:298px;height:298px;border-radius:50%;background:linear-gradient(150deg,#e9c7b6,#b58a78 60%,#3a4a6a)"></div>
    <h2 class="display abs" style="left:125px;top:1422px;font-size:25px">OUR TECHNOLOGY</h2>
    <p class="body-copy abs" style="left:126px;top:1470px;width:430px">Speckleplethysmography (SPG) and photoplethysmography (PPG) are both optical techniques used to measure physiological parameters like tissue oxygenation, but they differ in their underlying principles and practical advantages. SPG, which leverages laser speckle contrast imaging, offers some distinct benefits over PPG, especially in specific contexts for assessing tissue oxygenation. Here's a breakdown of those advantages based on how they work and their real-world implications.</p>
    <a class="btn" style="left:126px;top:1684px;width:191px;height:57px">READ MORE</a>
    <div class="abs" style="left:0;top:1844px;width:1200px;height:1px;background:var(--line)"></div>
  </section>

  <section class="features">
    <p class="abs" style="left:0;width:1200px;top:1933px;text-align:center;font-size:18px;font-weight:700">Advanced Technology</p>
    <h2 class="display grad-text abs" style="left:0;width:1200px;top:1972px;text-align:center;font-size:31px;line-height:42px">INNOVATIVE BLOOD<br>LOSS MONITORING</h2>
    <div class="feature" style="left:120px;top:2101px">
      <div class="feature-icon"><svg width="44" height="56" viewBox="0 0 44 56" fill="none" stroke="#fff" stroke-width="3"><rect x="8" y="4" width="28" height="48" rx="5"/><line x1="19" y1="44" x2="25" y2="44"/></svg></div>
      <h3>Portable Monitoring</h3>
      <p>Compact, wearable devices that provide continuous blood loss monitoring anywhere, anytime.</p>
    </div>
    <div class="feature" style="left:454px;top:2101px">
      <div class="feature-icon"><svg width="60" height="60" viewBox="0 0 60 60" fill="none" stroke="#fff" stroke-width="3"><circle cx="30" cy="30" r="26"/><polyline points="30,14 30,32 42,32"/></svg></div>
      <h3>Real-time Alerts</h3>
      <p>Instant notifications to caregivers when critical thresholds are reached.</p>
    </div>
    <div class="feature" style="left:796px;top:2101px">
      <div class="feature-icon"><svg width="62" height="56" viewBox="0 0 62 56" fill="none" stroke="#fff" stroke-width="3"><circle cx="24" cy="18" r="12"/><path d="M4 50c0-12 9-20 20-20s20 8 20 20"/><line x1="50" y1="20" x2="50" y2="34"/><line x1="43" y1="27" x2="57" y2="27"/></svg></div>
      <h3>Patient-Centered</h3>
      <p>Easy-to-use interface designed for both patients and healthcare providers.</p>
    </div>
  </section>

  <section class="early">
    <div class="abs" style="left:0;top:2450px;width:1200px;height:1px;background:var(--line)"></div>
    <div class="abs" style="left:0;top:2451px;width:470px;height:538px;background:linear-gradient(120deg,var(--cyan),var(--blue) 50%,var(--violet))"></div>
    <svg class="abs" style="left:400px;top:2451px" width="200" height="538" viewBox="0 0 200 538" aria-hidden="true">
      <path d="M55 0Q0 80 20 270Q45 470 70 538H200V0Z" fill="var(--navy)"/>
    </svg>
    <div class="ring" style="left:203px;top:2538px;width:400px;height:400px"></div>
    <div class="ring" style="left:221px;top:2556px;width:364px;height:364px;border-width:2px"></div>
    <div class="photo" role="img" aria-label="Digital blood pressure monitor"
      style="left:254px;top:2589px;width:298px;height:298px;border-radius:50%;background:linear-gradient(150deg,#f1f2f5,#c9cdd6 55%,#7e8797)"></div>
    <h2 class="display abs" style="left:631px;top:2534px;font-size:25px;line-height:34px">EARLY DETECTION<br>CAPABILITIES</h2>
    <p class="body-copy abs" style="left:632px;top:2620px;width:420px">Clinical studies have demonstrated the Lumeva device's ability to detect hemorrhage progression significantly earlier than conventional monitoring methods. The system's continuous monitoring capability enables healthcare providers to:</p>
    <ul class="checks abs" style="left:662px;top:2734px">
      <li>Identify subtle changes in tissue perfusion</li>
      <li>Monitor treatment effectiveness in real-time</li>
      <li>Make timely, data-driven clinical decisions</li>
      <li>Improve patient outcomes through early intervention</li>
    </ul>
    <a class="btn" style="left:658px;top:2866px;width:175px;height:56px">CONTACT</a>
    <div class="abs" style="left:0;top:2989px;width:1200px;height:1px;background:var(--violet)"></div>
  </section>

  <section class="team">
    <h2 class="display grad-text abs" style="left:0;width:1200px;top:3146px;text-align:center;font-size:25px">ABOUT OUR TEAM</h2>
    <div class="member" style="left:164px;top:3217px">
      <div class="avatar" role="img" aria-label="Portrait of a team member"><div></div></div>
      <h4>ELIAS MORROW<br>Founder</h4>
    </div>
    <div class="member" style="left:481px;top:3217px">
      <div class="avatar" role="img" aria-label="Portrait of a team member"><div></div></div>
      <h4>DANIEL REYES<br>Founder</h4>
    </div>
    <div class="member" style="left:793px;top:3217px">
      <div class="avatar" role="img" aria-label="Portrait of a team member"><div></div></div>
      <h4>OMAR HADDAD<br>Founder</h4>
    </div>
  </section>

  <section class="contact">
    <div class="abs" style="left:0;top:3605px;width:1200px;height:530px;background:linear-gradient(100deg,var(--cyan),var(--blue) 45%,var(--violet))"></div>
    <h2 class="display abs" style="left:126px;top:3702px;font-size:25px">CONTACT US</h2>
    <p class="abs" style="left:127px;top:3752px;font-size:15.5px">Call Us: 555 010 2741</p>
    <div class="field" style="left:127px;top:3800px;width:207px;height:40px;padding-top:10px">Name:</div>
    <div class="field" style="left:342px;top:3800px;width:207px;height:40px;padding-top:10px">Email:</div>
    <div class="field" style="left:127px;top:3856px;width:207px;height:40px;padding-top:10px">Phone:</div>
    <div class="field" style="left:342px;top:3856px;width:207px;height:40px;padding-top:10px">Subject:</div>
    <div class="field" style="left:127px;top:3912px;width:424px;height:96px">Message:</div>
    <a class="btn" style="left:127px;top:4036px;width:152px;height:56px;background:var(--navy)">SUBMIT</a>
    <div class="ring" style="left:653px;top:3649px;width:456px;height:456px;border-color:rgba(255,255,255,.7)"></div>
    <div class="ring" style="left:668px;top:3664px;width:426px;height:426px;border-width:2px;border-color:rgba(255,255,255,.6)"></div>
    <div class="photo" role="img" aria-label="Photo of an open hand holding a red heart"
      style="left:680px;top:3676px;width:402px;height:402px;border-radius:50%;background:linear-gradient(160deg,#e3e7ee,#b7bfcc 55%,#8a93a6)"></div>
  </section>

  <footer class="footer">
    <div class="brand" style="left:127px;top:4222px;font-size:32px">
      <span class="brand-dot" style="width:66px;height:66px"></span>LUMEVA
    </div>
    <div class="foot-col abs" style="left:470px;top:4226px">
      <h5>COMPANY</h5><p>About Lumeva</p><p>Press</p>
    </div>
    <div class="foot-col abs" style="left:660px;top:4226px">
      <h5>CONTACT</h5>
      <p><svg width="24" height="18" viewBox="0 0 24 18" fill="none" stroke="#4a8ff0" stroke-width="2"><rect x="1" y="1" width="22" height="16" rx="2"/><polyline points="1,2 12,10 23,2"/></svg>info@lumeva.com</p>
      <p><svg width="22" height="22" viewBox="0 0 24 24" fill="none" stroke="#4a8ff0" stroke-width="2"><path d="M5 2h4l2 5-3 2a12 12 0 0 0 7 7l2-3 5 2v4a2 2 0 0 1-2 2A19 19 0 0 1 3 4a2 2 0 0 1 2-2z"/></svg>Call: 555 014 8830</p>
    </div>
    <div class="foot-col abs" style="left:913px;top:4226px">
      <h5>LEGAL</h5><p>Privacy Policy</p><p>Terms of Service</p>
    </div>
    <div class="abs" style="left:127px;top:4392px;width:945px;height:1px;background:#3a3f7a"></div>
    <p class="abs" style="left:0;width:1200px;top:4432px;text-align:center;font-size:15px">2025 Lumeva. All rights reserved.</p>
    <span class="social" style="left:962px" role="img" aria-label="Social profile"></span>
    <span class="social" style="left:1024px" role="img" aria-label="Social profile"></span>
  </footer>

</div>
</body>
</html>
```